BrivoTerna. Lantern of the Steady Harvest. Business card

Professional business card for BrivoTerna (Lantern of the Steady Harvest)
My rationale: Strategy-> Execution-> Results-> Value that lead to the BrivoTerna name: We put the Lantern of the Steady Harvest.
We deliver value to our customers helping them at defining a good strategy (cyan arrow). 90% of well formulated strategies fail due to poor execution so we also consider strategical execution very important (green arrow). Due to the execution we obtain the results (blue arrow). Finally, the results provide feedback to redefine strategy, and the new strategy has to be executed and new results obtained providing new feedback and on and on. It's like a wheel that finally, must create corporate value: value for shareholders, staholders, employees, providers...-

Target Market(s)

CEOs and steering comitees , invewrnent funds

Industry/Entity Type

Business Consultant

Contact Information for Business Card

Teodoro Vinsquel
CEO & Founder
teodoro.vinsquel@brivoterna-example.com
Mobile: +34 655.803.912
www.brivoterna-example.com

Colors

Designer to choose colors to be used in the design.

Requirements
Nice to have
• Nice to hace the words: Strategy, execution, results
• Nice to vave the claim: Lantern of the Steady Harvest
• The three colors should be shown:
• cyan for STRATEGY
• green for EXECUTION
• blue for RESULTS
Should not have
• Complete black background

```html
<!DOCTYPE html>
<html lang="en">
<head>
<meta charset="utf-8">
<title>BrivoTerna – Business Card</title>
<link rel="stylesheet" href="https://fonts.googleapis.com/css2?family=PT+Sans:wght@400;700&display=swap">
<style>
  :root {
    --backdrop: #e4e6ea;
    --card-white: #ffffff;
    --brand-blue: #0b35a3;
    --brand-navy: #12318f;
    --exec-green: #8cc63f;
    --strategy-cyan: #19aee8;
    --text-grey: #3a3a3a;
    --rule-grey: #d3d6dc;
  }
  * { margin: 0; padding: 0; box-sizing: border-box; }
  html, body {
    width: 1200px;
    height: 900px;
    overflow: hidden;
    background: var(--backdrop);
    font-family: "PT Sans", Arial, sans-serif;
  }
  .canvas { position: relative; width: 1200px; height: 900px; }

  .card {
    position: absolute;
    width: 540px;
    height: 310px;
    border-radius: 22px;
    overflow: hidden;
    box-shadow: 0 10px 28px rgba(20, 30, 60, 0.22);
  }

  /* Front */
  .card-front { left: 110px; top: 100px; background: var(--card-white); }
  .front-wordmark {
    position: absolute;
    left: 40px; top: 78px;
    font-size: 52px;
    font-weight: 700;
    letter-spacing: -1.5px;
    color: var(--brand-blue);
  }
  .contact { position: absolute; left: 42px; top: 150px; color: var(--text-grey); }
  .contact-name { font-size: 17px; font-weight: 700; color: var(--brand-blue); line-height: 1.1; }
  .contact-role { font-size: 14px; margin-bottom: 8px; }
  .contact-line { display: flex; align-items: center; gap: 7px; font-size: 14px; line-height: 1.45; }
  .contact-line svg { width: 12px; height: 12px; fill: var(--brand-blue); flex: none; }
  .contact-rule {
    position: absolute; left: 42px; right: 40px; top: 236px;
    height: 1px; background: var(--rule-grey);
  }
  .contact-web { position: absolute; left: 42px; top: 240px; font-size: 15px; color: var(--text-grey); }
  .contact-web .web-domain { color: var(--strategy-cyan); }

  .tagline-band {
    position: absolute; left: 0; right: 0; bottom: 0;
    height: 38px;
    background: var(--brand-navy);
    border-top: 4px solid var(--exec-green);
    display: flex; align-items: center;
    padding-left: 40px;
    font-size: 15px; font-weight: 700; letter-spacing: 1.2px;
    color: var(--strategy-cyan);
  }
  .tagline-band .dot { margin: 0 10px; }

  /* Back */
  .card-back {
    left: 560px; top: 480px;
    background: var(--brand-blue);
    display: flex; align-items: center; justify-content: center;
  }
  .back-wordmark {
    font-size: 60px;
    font-weight: 700;
    letter-spacing: -1.5px;
    color: var(--card-white);
  }
</style>
</head>
<body>
<main class="canvas">

  <section class="card card-front" aria-label="Business card front">
    <div class="front-wordmark">BrivoTerna</div>

    <div class="contact">
      <div class="contact-name">Teodoro Vinsquel</div>
      <div class="contact-role">CEO &amp; Founder</div>
      <div class="contact-line">
        <svg viewBox="0 0 24 24" aria-hidden="true"><path d="M6.6 10.8a15.1 15.1 0 0 0 6.6 6.6l2.2-2.2c.3-.3.7-.4 1-.2 1.1.4 2.3.6 3.6.6.6 0 1 .4 1 1V20c0 .6-.4 1-1 1A17 17 0 0 1 3 4c0-.6.4-1 1-1h3.5c.6 0 1 .4 1 1 0 1.3.2 2.5.6 3.6.1.3 0 .7-.2 1z"/></svg>
        <span>+34 655.803.912</span>
      </div>
      <div class="contact-line">
        <svg viewBox="0 0 24 24" aria-hidden="true"><path d="M2 5h20v14H2zm2 2v.4l8 5 8-5V7zm0 2.8V17h16V9.8l-8 5z"/></svg>
        <span>teodoro.vinsquel@brivoterna-example.com</span>
      </div>
    </div>

    <div class="contact-rule"></div>
    <div class="contact-web">www.<span class="web-domain">brivoterna-example</span>.com</div>

    <div class="tagline-band">
      <span>RESULTS</span><span class="dot">•</span><span>EXECUTION</span><span class="dot">•</span><span>STRATEGY</span>
    </div>
  </section>

  <section class="card card-back" aria-label="Business card back">
    <div class="back-wordmark">BrivoTerna</div>
  </section>

</main>
</body>
</html>
```